Briloran Clear Springs needs a new business card design (we produce and sell pure bottled water)

We need a clean modern design for our new business cards, We have an existing logo which ultimately cannot be changed, however it could be slighty improved and the colours adjusted. We have this existing logo on all of our bottles, vehicles etc.

Our company slogan is "Clear from source to sip".
Along with our relevant company information
(Address, phone, website email etc) we will only be using names and not putting position titles for flexibilty.

We are looking for a clean, minimalist modern design.

You can view our website (if need of an update also!) to see our business.

Industry/Entity Type

Business

Contact Information for Business Card

Staff Name : XXXXXX XXXXXX
Address : 9/41 Tavenor St
Halden Rise QLD 4172
Staff Mobile Number : 04XX XXX XXX
Office Phone Number : 07 3918 2457
Staff Email Address : XXXX@brilorancleargo.com.au
Website : www.brilorancleargo.com.au

Font styles to use
Sans Serif

Colors
cee9f5
33a6d7
0492cd
0455a3
3276b5
85abd2
cedeed

Requirements
Must have
• The ability to edit and change the staff members details as we will need to edit for each respective staff member (7 in total)

```html
<!DOCTYPE html>
<html lang="en">
<head>
<meta charset="utf-8">
<title>Briloran Clear Springs – Business Card</title>
<link rel="stylesheet" href="https://fonts.googleapis.com/css2?family=Source+Sans+3:wght@400;600&display=swap">
<style>
  :root {
    --backdrop: #e8e8e8;
    --card-blue: #3276b5;
    --card-black: #000000;
    --ink-light: #ffffff;
    --rule: rgba(255,255,255,0.28);
    --brand-blue: #3276b5;
  }
  * { margin: 0; padding: 0; box-sizing: border-box; }
  html, body {
    width: 1200px; height: 900px; overflow: hidden;
    background: var(--backdrop);
    font-family: "Source Sans 3", "Myriad Pro", Arial, sans-serif;
  }
  .stage { position: relative; width: 1200px; height: 900px; }

  .card { position: absolute; top: 275px; width: 477px; height: 294px; overflow: hidden; }
  .card-front {
    left: 116px; background: var(--card-blue); color: var(--ink-light);
    border-radius: 0 48px 0 48px;
  }
  .card-back {
    left: 622px; background: var(--card-black);
    border-radius: 48px 0 48px 0;
    display: flex; align-items: center; justify-content: center;
  }

  .bottle-visual {
    position: absolute; left: 40px; top: 18px; width: 134px; height: 232px;
    border-radius: 30px 30px 14px 14px;
    background: linear-gradient(180deg, rgba(120,165,215,0.35), rgba(80,130,190,0.18));
  }

  .brand-front {
    position: absolute; right: 38px; top: 84px;
    display: flex; align-items: center; gap: 8px;
  }
  .brand-name { font-weight: 600; font-size: 21px; line-height: 1; letter-spacing: 0.2px; }
  .brand-dot { width: 12px; height: 12px; border-radius: 50%; background: currentColor; }

  .tagline {
    position: absolute; right: 36px; top: 157px;
    font-size: 12px; letter-spacing: 0.2px; text-transform: uppercase;
  }
  .staff-name {
    position: absolute; left: 36px; top: 150px;
    font-size: 18px; font-weight: 600;
  }
  .divider {
    position: absolute; left: 36px; right: 28px; top: 185px;
    height: 1px; background: var(--rule);
  }
  .address {
    position: absolute; left: 36px; top: 197px;
    font-size: 14px; line-height: 17.5px; font-style: normal;
  }
  .contacts {
    position: absolute; right: 26px; top: 199px; list-style: none;
    font-size: 14px; line-height: 19px; text-align: right;
  }
  .contacts li { display: flex; align-items: center; justify-content: flex-end; gap: 10px; }
  .contacts .icon { width: 9px; height: 9px; fill: var(--ink-light); flex: none; }
  .contacts .no-icon { padding-right: 19px; margin-top: 1px; }

  .brand-back { display: flex; align-items: center; gap: 10px; color: var(--brand-blue); }
  .brand-back .brand-name { font-size: 28px; }
  .brand-back .brand-dot { width: 16px; height: 16px; }
</style>
</head>
<body>
<main class="stage">
  <section class="card card-front" aria-label="Business card front">
    <div class="bottle-visual" role="img" aria-label="Faint photo of a large water cooler bottle"></div>

    <div class="brand-front">
      <span class="brand-name">Briloran Clear Springs</span>
      <span class="brand-dot" aria-hidden="true"></span>
    </div>
    <p class="tagline">Clear from source to sip</p>

    <h1 class="staff-name">Marcus Delaney</h1>
    <div class="divider"></div>

    <address class="address">9/41 Tavenor St<br>Halden Rise QLD 4172</address>

    <ul class="contacts">
      <li>0400 582 913
        <svg class="icon" viewBox="0 0 10 10" aria-hidden="true"><path d="M2.5 0h5a1 1 0 0 1 1 1v8a1 1 0 0 1-1 1h-5a1 1 0 0 1-1-1V1a1 1 0 0 1 1-1zm.6 1.2v6.6h3.8V1.2z"/></svg>
      </li>
      <li>07 3918 2457
        <svg class="icon" viewBox="0 0 10 10" aria-hidden="true"><path d="M2 0.3l1.6 2-1 1.1c.6 1.3 1.6 2.4 3 3l1.1-1 2 1.6-.9 1.9C4.4 8.6 1.3 5.6.2 2z"/></svg>
      </li>
      <li>info@brilorancleargo.com.au
        <svg class="icon" viewBox="0 0 10 10" aria-hidden="true"><path d="M0 2h10v.6L5 5.6 0 2.6zm0 1.6l5 3 5-3V8H0z"/></svg>
      </li>
      <li class="no-icon">www.brilorancleargo.com.au</li>
    </ul>
  </section>

  <section class="card card-back" aria-label="Business card back">
    <div class="brand-back">
      <span class="brand-name">Briloran Clear Springs</span>
      <span class="brand-dot" aria-hidden="true"></span>
    </div>
  </section>
</main>
</body>
</html>
```